Brindlewick Solutions Ltd

I'd like to create a company letterhead for the attached logo in word format.

I'd like to emphasis the icon in large translucent state from the left corner and ensure that the letterhead colouring matches the colour palette of the current logo with a contrast so it's clear to see. I've attached a copy of our sister company page on the app for reference.

```html
<!DOCTYPE html>
<html lang="en">
<head>
<meta charset="utf-8">
<title>Brindlewick Solutions Ltd — Letterhead</title>
<link rel="stylesheet" href="https://fonts.googleapis.com/css2?family=Montserrat:wght@500&family=Open+Sans:wght@400;600&display=swap">
<style>
  :root {
    --backdrop: #e4e4e4;
    --paper: #f4f4f4;
    --teal: #3fb3a0;
    --teal-deep: #2fa08e;
    --stripe-grey: #a9a9a9;
    --ink-grey: #8a8a8a;
    --watermark: rgba(63, 179, 160, 0.06);
    --white: #ffffff;
  }
  * { box-sizing: border-box; margin: 0; padding: 0; }
  html, body {
    width: 1200px;
    height: 800px;
    overflow: hidden;
    background: var(--backdrop);
  }
  .canvas {
    position: relative;
    width: 1200px;
    height: 800px;
  }
  .letterhead {
    position: absolute;
    left: 345px;
    top: 40px;
    width: 510px;
    height: 720px;
    background: var(--paper);
    overflow: hidden;
    box-shadow: 0 6px 18px rgba(0, 0, 0, 0.12);
  }
  .watermark-disc {
    position: absolute;
    left: -150px;
    top: 160px;
    width: 340px;
    height: 340px;
    border-radius: 50%;
    background: var(--watermark);
  }
  .brand {
    position: absolute;
    left: 38px;
    top: 34px;
    display: flex;
    align-items: center;
    gap: 10px;
    color: var(--teal);
    font-family: "Montserrat", sans-serif;
    font-weight: 500;
  }
  .brand-dot {
    width: 30px;
    height: 30px;
    border-radius: 50%;
    background: var(--teal);
  }
  .brand-name {
    font-size: 23px;
    line-height: 1;
  }
  .brand-tagline {
    display: block;
    margin-top: 4px;
    font-size: 7px;
    letter-spacing: 3.2px;
  }
  .contact {
    position: absolute;
    right: 30px;
    top: 30px;
    width: 150px;
    font-family: "Open Sans", sans-serif;
    font-size: 8px;
    line-height: 1.45;
    color: var(--ink-grey);
  }
  .contact-line {
    display: flex;
    align-items: center;
    gap: 5px;
  }
  .contact-icon {
    width: 9px;
    height: 9px;
    flex: none;
  }
  .footer-band {
    position: absolute;
    left: 0;
    bottom: 0;
    width: 510px;
    height: 180px;
  }
  .website {
    position: absolute;
    right: 22px;
    bottom: 78px;
    font-family: "Open Sans", sans-serif;
    font-size: 8.5px;
    color: var(--white);
    letter-spacing: 0.2px;
  }
</style>
</head>
<body>
  <main class="canvas">
    <article class="letterhead">
      <div class="watermark-disc" aria-hidden="true"></div>

      <header class="brand">
        <span class="brand-dot" aria-hidden="true"></span>
        <span class="brand-name">Brindlewick<span class="brand-tagline">SOLUTIONS LTD</span></span>
      </header>

      <address class="contact">
        <div class="contact-line">Suite 102 Street name,</div>
        <div class="contact-line">State, ZIP 2034, Country</div>
        <div class="contact-line">
          <svg class="contact-icon" viewBox="0 0 10 10" aria-hidden="true">
            <circle cx="5" cy="5" r="5" fill="#3fb3a0"/>
            <path d="M3.3 2.6 L4.2 2.4 L4.7 3.7 L4.1 4.1 Q4.6 5.3 5.9 5.9 L6.3 5.3 L7.6 5.8 L7.4 6.7 Q4 7 3.3 2.6Z" fill="#fff"/>
          </svg>
          (00) 09876 543 210
        </div>
        <div class="contact-line">
          <svg class="contact-icon" viewBox="0 0 10 10" aria-hidden="true">
            <circle cx="5" cy="5" r="5" fill="#3fb3a0"/>
            <rect x="2.6" y="3.3" width="4.8" height="3.4" fill="#fff"/>
            <path d="M2.6 3.3 L5 5.2 L7.4 3.3" fill="none" stroke="#3fb3a0" stroke-width="0.6"/>
          </svg>
          office@brindlewick.example
        </div>
      </address>

      <svg class="footer-band" viewBox="0 0 510 180" aria-hidden="true">
        <path d="M0 146 C180 146 300 118 392 70 L404 84 L416 64 C450 56 480 52 510 50 L510 180 L0 180 Z" fill="var(--stripe-grey)"/>
        <path d="M0 156 C180 156 300 128 392 80 L404 94 L416 74 C450 66 480 62 510 60 L510 180 L0 180 Z" fill="var(--teal)"/>
      </svg>
      <p class="website">www.brindlewick.example</p>
    </article>
  </main>
</body>
</html>
```